Indy Film Production Company/Studio

We need a business card designed from an existing logo. We are a digital studio/production company that caters to creating genre entertainment, like Action, Horror, and martial arts. The card along with the logo will be used to Brand the company from letter heads to banners. The design will also be used for postcards and Brochures. It should be professional and masculine.
Updates

Thank you to all the designers who have participated. I'm narrowing down who it will be. Thank you again.

Target Market(s)

Investors, Networks, Producers, and actors

Industry/Entity Type

Film Production

Contact Information for Business Card

Teodoro Valbuena
Producer/Writer/Director
www.kestrelpicturehouse.example

Requirements
Must have
• Website address, Facebook icon and Twitter icon possibly in the back of the card.
Nice to have
• Logline of Company: Follow The Action.

```html
<!DOCTYPE html>
<html lang="en">
<head>
<meta charset="utf-8">
<title>Kestrel Picture House – Business Card</title>
<link rel="stylesheet" href="https://fonts.googleapis.com/css2?family=Roboto+Condensed:wght@400;700&family=Open+Sans:ital,wght@0,400;1,400&display=swap">
<style>
  :root {
    --stage: #3a3a3a;
    --paper: #f7f7f7;
    --brand-red: #e31b23;
    --brand-red-dark: #c9141b;
    --ink: #222222;
    --ink-soft: #555555;
    --white: #ffffff;
  }
  * { margin: 0; padding: 0; box-sizing: border-box; }
  html, body {
    width: 1200px; height: 750px; overflow: hidden;
    background: var(--stage);
  }
  .canvas { position: relative; width: 1200px; height: 750px; }

  .card {
    position: absolute; left: 371px; width: 461px; height: 263px;
    overflow: hidden;
  }
  .card--front { top: 81px; background: var(--paper); }
  .card--back  { top: 382px; background: var(--brand-red); }

  /* Front */
  .front-frame {
    position: absolute; inset: 8px;
    border: 2px solid var(--brand-red);
  }
  .corner { position: absolute; }
  .corner--top-right { top: 8px; right: 8px; }
  .corner--bottom-left { bottom: 8px; left: 8px; }

  .brand-name {
    position: absolute; left: 25px; top: 26px;
    font-family: "Roboto Condensed", sans-serif; font-weight: 700;
    color: var(--brand-red); text-transform: uppercase;
    font-size: 30px; line-height: 30px; letter-spacing: 0.5px;
  }

  .person {
    position: absolute; right: 26px; top: 112px; text-align: right;
    font-family: "Roboto Condensed", sans-serif; text-transform: uppercase;
  }
  .person__name { color: var(--brand-red); font-size: 18px; line-height: 20px; font-weight: 400; }
  .person__role { color: var(--ink); font-size: 13px; line-height: 18px; font-weight: 700; }

  .contact-list {
    position: absolute; right: 27px; top: 157px; list-style: none;
    font-family: "Open Sans", sans-serif; font-size: 12.5px; color: var(--ink-soft);
  }
  .contact-list li {
    display: flex; justify-content: flex-end; align-items: center;
    height: 17.6px; gap: 6px;
  }
  .contact-list svg { width: 11px; height: 11px; flex: none; }

  /* Back */
  .camera-photo {
    position: absolute; inset: 0;
    background: radial-gradient(ellipse at 50% 45%, #d61a22 0%, #e11b23 55%, var(--brand-red) 100%);
  }
  .back-brand {
    position: absolute; left: 0; right: 0; top: 94px; text-align: center;
    font-family: "Roboto Condensed", sans-serif; font-weight: 700;
    color: var(--white); text-transform: uppercase;
    font-size: 30px; line-height: 30px;
  }
  .back-web {
    position: absolute; left: 0; right: 0; top: 164px; text-align: center;
    font-family: "Open Sans", sans-serif; font-style: italic;
    color: var(--white); font-size: 13px;
  }
</style>
</head>
<body>
<main class="canvas">

  <section class="card card--front" aria-label="Business card front">
    <div class="front-frame"></div>
    <svg class="corner corner--top-right" width="56" height="56" viewBox="0 0 56 56" aria-hidden="true">
      <polygon points="0,0 56,0 56,56" fill="var(--brand-red)"/>
    </svg>
    <svg class="corner corner--bottom-left" width="56" height="56" viewBox="0 0 56 56" aria-hidden="true">
      <polygon points="0,0 56,56 0,56" fill="var(--brand-red)"/>
    </svg>

    <div class="brand-name">Kestrel<br>Picture House</div>

    <div class="person">
      <p class="person__name">Teodoro Valbuena</p>
      <p class="person__role">Producer/Writer/Director</p>
    </div>

    <ul class="contact-list">
      <li>555 014 2290
        <svg viewBox="0 0 12 12" aria-hidden="true"><path d="M2.5 1 L4.5 1 L5.3 3.6 L4 4.6 C4.7 6 5.9 7.3 7.4 8 L8.4 6.7 L11 7.5 L11 9.5 C11 10.4 10.3 11 9.5 11 C5 10.6 1.4 7 1 2.5 C1 1.7 1.6 1 2.5 1 Z" fill="var(--brand-red)"/></svg>
      </li>
      <li>hello@kestrelmail.example
        <svg viewBox="0 0 12 12" aria-hidden="true"><rect x="0.5" y="2.5" width="11" height="7" fill="var(--brand-red)"/><path d="M0.8 2.8 L6 6.6 L11.2 2.8" stroke="var(--white)" stroke-width="1" fill="none"/></svg>
      </li>
      <li>www.kestrelpicturehouse.example
        <svg viewBox="0 0 12 12" aria-hidden="true"><circle cx="6" cy="6" r="5.5" fill="var(--brand-red)"/><ellipse cx="6" cy="6" rx="2.3" ry="5.3" stroke="var(--white)" stroke-width="0.8" fill="none"/><line x1="0.7" y1="6" x2="11.3" y2="6" stroke="var(--white)" stroke-width="0.8"/></svg>
      </li>
      <li>kestrelpicturehouse.example
        <svg viewBox="0 0 12 12" aria-hidden="true"><rect x="0.5" y="0.5" width="11" height="11" fill="var(--brand-red)"/></svg>
      </li>
      <li>@kestrelpicturehouse
        <svg viewBox="0 0 12 12" aria-hidden="true"><rect x="0.5" y="0.5" width="11" height="11" fill="var(--brand-red)"/></svg>
      </li>
    </ul>
  </section>

  <section class="card card--back" aria-label="Business card back">
    <div class="camera-photo" role="img" aria-label="Red-tinted photograph of a cinema camera with lens and follow focus"></div>
    <div class="back-brand">Kestrel Picture House</div>
    <p class="back-web">www.kestrelpicturehouse.example</p>
  </section>

</main>
</body>
</html>
```